Tall Fern Roofing Business Card

Need a business card with the logo that was designed here

Contact Information for Business Card

Name, Title, Phone, Email, Website, Company name

```html
<!DOCTYPE html>
<html lang="en">
<head>
<meta charset="utf-8">
<title>Tall Fern Roofing – Business Card</title>
<link rel="stylesheet" href="https://fonts.googleapis.com/css2?family=Poppins:wght@400;600;700&display=swap">
<style>
  :root {
    --page-bg: #c4c4c4;
    --card-white: #ffffff;
    --brand-blue: #1b75bc;
    --brand-blue-deep: #155f99;
    --brand-blue-light: #2f8fe0;
    --text-grey: #4a4a4a;
    --rule-grey: #d9d9d9;
  }
  * { box-sizing: border-box; margin: 0; padding: 0; }
  html, body {
    width: 1093px;
    height: 1200px;
    overflow: hidden;
  }
  body {
    background: var(--page-bg);
    font-family: "Poppins", sans-serif;
    position: relative;
  }
  .card {
    position: absolute;
    left: 264px;
    border-radius: 27px;
  }
  .card-front {
    top: 226px;
    width: 577px;
    height: 356px;
    background: var(--card-white);
  }
  .card-back {
    top: 621px;
    width: 582px;
    height: 356px;
    background: var(--brand-blue);
    display: flex;
    align-items: center;
    justify-content: center;
  }
  .brand {
    display: flex;
    align-items: center;
    gap: 10px;
    font-weight: 600;
    font-size: 30px;
    line-height: 1;
    white-space: nowrap;
  }
  .brand-mark {
    width: 16px;
    height: 16px;
    flex: none;
  }
  .card-front .brand {
    position: absolute;
    left: 245px;
    top: 97px;
    color: var(--brand-blue);
  }
  .card-front .brand-mark { background: var(--brand-blue); }
  .card-back .brand {
    font-size: 36px;
    color: var(--brand-blue-deep);
    margin-top: 6px;
  }
  .card-back .brand-mark { background: var(--brand-blue-deep); width: 19px; height: 19px; }
  .person {
    position: absolute;
    left: 31px;
    top: 204px;
  }
  .person-name {
    font-weight: 700;
    font-size: 21px;
    line-height: 1.1;
    color: var(--brand-blue);
    letter-spacing: 0.2px;
  }
  .person-title {
    font-weight: 400;
    font-size: 17px;
    line-height: 1.15;
    color: var(--text-grey);
  }
  .divider {
    position: absolute;
    left: 32px;
    top: 256px;
    width: 505px;
    height: 1px;
    background: var(--rule-grey);
  }
  .contact-list {
    position: absolute;
    left: 31px;
    top: 272px;
    list-style: none;
  }
  .contact-item {
    display: flex;
    align-items: center;
    gap: 7px;
    font-size: 17px;
    line-height: 21px;
    color: var(--text-grey);
  }
  .contact-item svg { width: 15px; height: 15px; flex: none; }
  .website {
    position: absolute;
    right: 38px;
    top: 293px;
    font-size: 17px;
    line-height: 21px;
    color: var(--text-grey);
  }
  .website .domain { color: var(--brand-blue); }
</style>
</head>
<body>
  <section class="card card-front" aria-label="Business card front">
    <div class="brand"><span class="brand-mark"></span>Tall Fern Roofing</div>

    <div class="person">
      <p class="person-name">DANIEL HARPER</p>
      <p class="person-title">Managing Director</p>
    </div>

    <div class="divider"></div>

    <ul class="contact-list">
      <li class="contact-item">
        <svg viewBox="0 0 16 16" aria-hidden="true">
          <path d="M3.2 1.5l2.4 2.6-1.3 1.9c.9 2 2.3 3.5 4.3 4.5l1.9-1.3 2.6 2.4-1.4 2.3C7 13.6 2.4 9 1 4.3z" fill="none" stroke="#1b75bc" stroke-width="1.8" stroke-linejoin="round"/>
          <path d="M9.5 1.8a5 5 0 0 1 4.7 4.7M9.3 4.3a2.6 2.6 0 0 1 2.4 2.4" fill="none" stroke="#1b75bc" stroke-width="1.3" stroke-linecap="round"/>
        </svg>
        <span>044-555 018 274</span>
      </li>
      <li class="contact-item">
        <svg viewBox="0 0 16 16" aria-hidden="true">
          <rect x="0.5" y="3" width="15" height="10" fill="#1b75bc"/>
          <path d="M0.8 3.4L8 9l7.2-5.6M0.8 12.6l5-4.4M15.2 12.6l-5-4.4" fill="none" stroke="#ffffff" stroke-width="1.1"/>
        </svg>
        <span>info@tallfernroofing.com</span>
      </li>
    </ul>

    <p class="website">www.<span class="domain">tallfernroofing</span>.com</p>
  </section>

  <section class="card card-back" aria-label="Business card back">
    <div class="brand"><span class="brand-mark"></span>Tall Fern Roofing</div>
  </section>
</body>
</html>
```